Satchel & Sundial needs new business card design

I need a new business card design. I'm looking for out-of-the-box design which represents the freedom of being a location independent entrepreneur.
I offer coaching, retreats and trips.
I would like to see designs with and without the photo.
Colors I use are black (#000000), green (#25A796) and brown (#D7C38C)
Website satchelandsundial.example

Target Market(s)

location independent entrepreneurs, digital nomads, people looking to swap the 9 to 5 for a lifestyle business

Industry/Entity Type

Business

Contact Information for Business Card

Dorota Falkner
Your Lifestyle Business Coach, Retreat & Trip Leader
http://satchelandsundial.example
hello@satchelandsundial.example
Live a life you don't need a holiday from

Font styles to use
Serif
Sans Serif

Requirements
Must have
• One side should contain only the logo. I would also consider having the "Live a life you don't need a holiday from" on that side too (depending on how it looks)
• Please show both sides on the designs.

```html
<!DOCTYPE html>
<html lang="en">
<head>
<meta charset="utf-8">
<title>Satchel &amp; Sundial – Business Card</title>
<link rel="stylesheet" href="https://fonts.googleapis.com/css2?family=Open+Sans:wght@400;600;700&display=swap">
<style>
  :root {
    --green: #21a796;
    --black: #1d1d1f;
    --white: #ffffff;
    --backdrop: #ececea;
    --ink: #222222;
  }
  * { box-sizing: border-box; margin: 0; padding: 0; }
  html, body {
    width: 1200px; height: 900px; overflow: hidden;
    background: var(--backdrop);
    font-family: "Open Sans", Arial, sans-serif;
  }
  .card {
    position: absolute; left: 280px;
    width: 640px; height: 366px;
    box-shadow: 0 6px 18px rgba(0,0,0,.18);
    overflow: hidden;
  }
  .card--front { top: 64px; background: var(--green); }
  .card--back { top: 470px; background: var(--white); }

  .wordmark {
    position: absolute;
    font-weight: 700; text-transform: uppercase;
    letter-spacing: 1px; white-space: nowrap;
    color: var(--black);
  }
  .card--front .wordmark { left: 0; right: 0; top: 152px; text-align: center; font-size: 44px; }
  .card--back .wordmark { right: 34px; top: 112px; font-size: 32px; line-height: 44px; }

  .card-shapes { position: absolute; inset: 0; }

  .identity { position: absolute; left: 70px; top: 20px; color: var(--ink); }
  .identity__name { font-size: 18px; font-weight: 700; line-height: 1.3; }
  .identity__first { color: var(--green); }
  .identity__role { font-size: 14px; line-height: 1.35; }

  .contacts { position: absolute; left: 30px; top: 180px; list-style: none; font-size: 14px; color: var(--ink); }
  .contacts li { display: flex; align-items: center; gap: 8px; line-height: 1.5; }
  .contacts svg { width: 12px; height: 12px; flex: none; }

  .tagline {
    position: absolute; left: 30px; top: 234px;
    font-size: 14px; text-transform: uppercase; letter-spacing: .3px; color: var(--ink);
  }
</style>
</head>
<body>

<section class="card card--front" aria-label="Card front">
  <div class="wordmark">Satchel &amp; Sundial</div>
</section>

<section class="card card--back" aria-label="Card back">
  <svg class="card-shapes" viewBox="0 0 640 366" aria-hidden="true">
    <polygon points="0,18 30,18 0,50" fill="var(--green)"/>
    <polygon points="34,18 60,18 60,50 20,50" fill="var(--black)"/>
    <polygon points="0,266 296,266 282,292 0,292" fill="var(--green)"/>
    <polygon points="304,270 640,270 640,346 262,346" fill="var(--black)"/>
  </svg>

  <div class="identity">
    <p class="identity__name"><span class="identity__first">Dorota</span> Falkner</p>
    <p class="identity__role">Your Lifestyle Business Coach</p>
    <p class="identity__role">Retreat &amp; Trip Leader</p>
  </div>

  <div class="wordmark">Satchel &amp; Sundial</div>

  <ul class="contacts">
    <li>
      <svg viewBox="0 0 12 12"><rect x="0.5" y="2" width="11" height="8" fill="var(--green)"/><polyline points="0.5,2 6,6.5 11.5,2" fill="none" stroke="#fff" stroke-width="1"/></svg>
      hello@satchelandsundial.example
    </li>
    <li>
      <svg viewBox="0 0 12 12"><circle cx="6" cy="6" r="5.5" fill="var(--green)"/><ellipse cx="6" cy="6" rx="2.2" ry="5" fill="none" stroke="#fff" stroke-width=".8"/><line x1="1" y1="6" x2="11" y2="6" stroke="#fff" stroke-width=".8"/></svg>
      www.satchelandsundial.example
    </li>
  </ul>

  <p class="tagline">Live a life you don't need a holiday from</p>
</section>

</body>
</html>
```